2 x Digitize Logo | 2 x Business Cards | 2 x Fridge Magnets

We require 6 deliverables:
1. Residential logo redrawn (same just high quality for large print format).
2. Corporate logo redrawn (minor changes to wording and high quality for large print format).
3. New business card design for Furniture Removals (residential)
4. New business card design for Corporate Relocations (business)
5. New Fridge magnet for Furniture removals (residential)
6. New fridge magnet for Corporate Relocations (business)
1. Residential Logo
a. We require the logo to be translated into a high quality digital image with no modifications.
(see attached resilogo.jpg)
2. Residential Logo
a. We require the logo to be edited (add the word corporate relocations) be translated into a high quality digital image.
(see attached corplogo.jpg)
3. Using the resilogo please make a new business card for our business.
a. Please see the web site https://www.larkbendcarters.com.au for colours and inspiration.
b. The residential business card needs the following information:
i. Business Name (using the residential logo).
ii. Free Call: 1800 LB Cart (the L, B and Cart much be the same colour as the logo).
iii. Website: www.LarkbendCarters.com.au
iv. Address: 4/17 Ormsdale Court, VIC 3264
v. Email: cart@LarkbendCarters.com.au
vi. backof Card:
Review our service
www.PennantOrbit.com.au
Services: Local, Country, Interstate | Furniture Removals | Piano, Billiard Tables & Antiques
4. Using the corplogo please make a new business card for our business.
b. The corporate business card needs the following information:
i. Business Name (using the corporate logo).
v. Email: corporate@LarkbendCarters.com.au
vi. Back of Card:
Review our service
www.PennantOrbit.com.au
Services: Corporate relocations | Office equipment moves | Packing Service | Packing Materials
5. Using the resilogo please make a new fridge magent for our business.
b. The residential fidge magnet needs the following information:
iv. Services: Local, Country, Interstate | Furniture Removals | Piano, Billiard Tables & Antiques
6. Using the corplogo please make a new fridge magent for our business.
b. The corporate fidge magnet needs the following information:
iv. Services: Local, Country, Interstate | Corporate relocations
Target Market(s)
Residential Furniture Removals and Corporate Office relocations
Industry/Entity Type
Business
Contact Information for Business Card
Please see full brief for six items required
Requirements
Must have
- Clean simple, easy to read
Nice to have
- fresh, stand out, eye catching
Should not have
- plain, standard, boring, general

```html
<!DOCTYPE html>
<html lang="en">
<head>
<meta charset="utf-8">
<title>Larkbend Carters – Business Cards</title>
<link rel="stylesheet" href="https://fonts.googleapis.com/css2?family=Open+Sans:wght@400;600;700&family=Fira+Sans+Condensed:wght@400;500;800&display=swap">
<style>
:root{
  --bg:#cbcbcb;
  --dark:#2b2b2b;
  --paper:#f6f6f4;
  --ink:#2a2a2a;
  --white:#ffffff;
  --yellow:#f2a300;
  --red:#e3231f;
  --green:#12913c;
  --rule:#9a9a9a;
}
*{margin:0;padding:0;box-sizing:border-box}
html,body{width:1200px;height:782px;overflow:hidden;background:var(--bg)}
.sheet{position:relative;width:1200px;height:782px}
.card{position:absolute;width:418px;height:252px;box-shadow:6px 8px 10px rgba(0,0,0,.22)}
.card--dark{background:var(--dark);color:var(--white)}
.card--light{background:var(--paper);color:var(--ink)}
.card--tl{left:165px;top:118px}
.card--tr{left:617px;top:118px}
.card--bl{left:165px;top:411px}
.card--br{left:617px;top:411px}

.brand{position:absolute;font-family:"Fira Sans Condensed",sans-serif;font-weight:800;text-transform:uppercase;white-space:nowrap;letter-spacing:.5px}
.brand--lg{font-size:38px;left:0;right:0;text-align:center}
.brand--sm{font-size:20px;text-align:center}
.brand__name{color:var(--green)}
.brand__tag{display:block;font-family:"Open Sans",sans-serif;font-weight:400;font-size:10px;letter-spacing:0;color:var(--green);margin-top:2px}

.review{position:absolute;left:0;right:0;text-align:center;font-family:"Open Sans",sans-serif}
.review__label{display:flex;align-items:center;justify-content:center;gap:12px;font-size:12px;color:#e6e6e6}
.review__label::before,.review__label::after{content:"";width:88px;height:2px;background:linear-gradient(90deg,transparent,var(--rule) 20%,var(--rule) 80%,transparent)}
.review__url{font-size:15.5px;margin-top:4px;color:var(--white)}
.c-y{color:var(--yellow);font-weight:700}
.c-r{color:var(--red);font-weight:700}
.c-g{color:var(--green);font-weight:700}

.services{position:absolute;left:0;right:0;text-align:center;font-family:"Fira Sans Condensed",sans-serif;font-weight:500;font-size:10.5px;color:var(--white);white-space:nowrap}
.services .sep{color:var(--yellow);margin:0 4px}

.person{position:absolute;left:20px;top:125px;font-family:"Open Sans",sans-serif}
.person__name{font-size:20.5px;font-weight:600;color:var(--ink)}
.person__role{font-family:"Fira Sans Condensed",sans-serif;font-size:10px;margin-top:1px}

.contact{position:absolute;left:20px;top:187px;list-style:none;font-family:"Fira Sans Condensed",sans-serif;font-size:10.5px}
.contact li{display:flex;align-items:center;height:15px}
.contact svg{width:10px;height:10px;margin-right:8px;flex:none}
.contact .site-a{color:var(--yellow)}
.contact .site-b{color:var(--green)}

.address{position:absolute;right:35px;top:206px;text-align:right;font-family:"Fira Sans Condensed",sans-serif;font-size:10.5px;line-height:14px}
</style>
</head>
<body>
<main class="sheet">

  <section class="card card--dark card--tl">
    <div class="brand brand--lg" style="top:52px"><span class="brand__name">Larkbend Carters</span></div>
    <div class="review" style="top:137px">
      <div class="review__label">Review our service</div>
      <div class="review__url">www.<span class="c-y">Pennant</span><span class="c-r">Orb</span><span class="c-g">it</span>.com.au</div>
    </div>
    <p class="services" style="top:223px">Local, Country, Interstate<span class="sep">|</span>Furniture Removals<span class="sep">|</span>Piano, Billiard Tables &amp; Antiques</p>
  </section>

  <section class="card card--light card--tr">
    <div class="brand brand--lg" style="top:30px;font-size:36px"><span class="brand__name">Larkbend Carters</span></div>
    <div class="person">
      <div class="person__name">R. Hensley</div>
      <div class="person__role">Managing Director</div>
    </div>
    <ul class="contact">
      <li><svg viewBox="0 0 10 10"><path fill="#12913c" d="M1 3.5C1 2 2.5 1.5 5 1.5S9 2 9 3.5L7.5 4 7 3H3L2.5 4zM2.5 5h5l1 3.5h-7z"/></svg>Free Call: 1800 <span class="site-a">LB</span>&nbsp;<span class="site-b">Cart</span></li>
      <li><svg viewBox="0 0 10 10"><rect x=".5" y="2" width="9" height="6.5" fill="#e3231f"/><path d="M.5 2 5 6 9.5 2" fill="none" stroke="#fff" stroke-width=".9"/></svg>cart@larkbendcarters.com.au</li>
      <li><svg viewBox="0 0 10 10"><circle cx="5" cy="5" r="4.3" fill="none" stroke="#12913c" stroke-width="1"/><path d="M.7 5h8.6M5 .7c-2.4 2.6-2.4 6 0 8.6M5 .7c2.4 2.6 2.4 6 0 8.6" fill="none" stroke="#12913c" stroke-width=".8"/></svg>www.<span class="site-a">Larkbend</span><span class="site-b">Carters</span>.com.au</li>
    </ul>
    <address class="address" style="font-style:normal">4/17 Ormsdale<br>Court, VIC 3264</address>
  </section>

  <section class="card card--dark card--bl">
    <div class="brand brand--sm" style="left:0;right:0;top:76px"><span class="brand__name">Larkbend Carters</span><span class="brand__tag">CORPORATE RELOCATIONS</span></div>
    <div class="review" style="top:176px">
      <div class="review__label">Review our service</div>
      <div class="review__url">www.<span class="c-y">Pennant</span><span class="c-r">Orb</span><span class="c-g">it</span>.com.au</div>
    </div>
    <p class="services" style="top:184px;top:183px;margin-top:40px">Corporate relocations | Office equipment moves | Packing Service | Packing Materials</p>
  </section>

  <section class="card card--light card--br">
    <div class="brand brand--sm" style="left:191px;width:200px;top:76px"><span class="brand__name">Larkbend Carters</span><span class="brand__tag">CORPORATE RELOCATIONS</span></div>
    <div class="person">
      <div class="person__name">R. Hensley</div>
      <div class="person__role">Managing Director</div>
    </div>
    <ul class="contact">
      <li><svg viewBox="0 0 10 10"><path fill="#12913c" d="M1 3.5C1 2 2.5 1.5 5 1.5S9 2 9 3.5L7.5 4 7 3H3L2.5 4zM2.5 5h5l1 3.5h-7z"/></svg>Free Call: 1800 <span class="site-a">LB</span>&nbsp;<span class="site-b">Cart</span></li>
      <li><svg viewBox="0 0 10 10"><rect x=".5" y="2" width="9" height="6.5" fill="#e3231f"/><path d="M.5 2 5 6 9.5 2" fill="none" stroke="#fff" stroke-width=".9"/></svg>corporate@larkbendcarters.com.au</li>
      <li><svg viewBox="0 0 10 10"><circle cx="5" cy="5" r="4.3" fill="none" stroke="#12913c" stroke-width="1"/><path d="M.7 5h8.6M5 .7c-2.4 2.6-2.4 6 0 8.6M5 .7c2.4 2.6 2.4 6 0 8.6" fill="none" stroke="#12913c" stroke-width=".8"/></svg>www.<span class="site-a">Larkbend</span><span class="site-b">Carters</span>.com.au</li>
    </ul>
    <address class="address" style="font-style:normal">4/17 Ormsdale<br>Court, VIC 3264</address>
  </section>

</main>
</body>
</html>
```